New design for www.TrimTable.com

On TrimTable you can find & book your hairdresser. TrimTable is the biggest platform in the Netherlands.

- The design should be a responcive design
- Should be able to go global, should fit in perfectly between all the big booking platforms like stayvo, ridlo etc,
- Should have te result of more bookings. :)
- We are ‘only’ asking a beautiful design, not a technical solution.
- We need a homepage (https://trimtable.com/), search resultpage ((https://trimtable.com/kapper/amsterdam/#), salonpage (https://trimtable.com/kapper/vorden/lumo-for-hair/), about us page (https://trimtable.com/aboutus/), for the hairdresser info page (https://trimtable.com/kapper/), login/register page (https://trimtable.com/account/signin/).

- On the page of the hairdresser there is a dynamic part. The part where you create your appointment. Please take a look at this part too after you choose your treatment (behandeling), employee (medewerker), Date (datum) and time (tijd). The part that you see after this, is the part where you fill in your data as a consumer.

I've added more logo's but mostly we use the green color.

A few of our competitors: www.plumsalo.com, www.korifex.com

Target Market(s)

All consumers

Industry/Entity Type

Hair And Beauty

Number of Pages Required

5+ page

Font styles to use
Sans Serif

Colors
abd036
c3c3c3
757575

Requirements
Must have
• Responsive
• We did an A/B test with the homepage. It turns out that option B works better then option A (take a look at the uploaded pictures). So what we need on the homepage: The USP's with the green checkboxes, The search button needs to by dynamic (changes for example from light green to dark green so you can see you can click it) The call to action sentence Zoek & Vind je kapsalon, the searchfield and searchbutton should be seperated.
Nice to have
• The style that we like is the flat design style. The website should be simple, clean and it should feel a bit like a luxury thing. Because an appointment with the hairdresser can be a real treat and luxury moment for yourself.
• The luxury feeling and flat design that is in the www.ridlo.com website is really nice for example. But then it has to be a bit more light and not so black and dark.

```html
<!DOCTYPE html>
<html lang="nl">
<head>
<meta charset="utf-8">
<title>TrimTable – Zoek &amp; vind je kapper</title>
<link rel="stylesheet" href="https://fonts.googleapis.com/css2?family=Montserrat:wght@400;600;700&family=Open+Sans:wght@400;600&display=swap">
<style>
:root{
  --green:#abd036;
  --green-dark:#8fb422;
  --orange:#f26a21;
  --grey:#757575;
  --grey-light:#c3c3c3;
  --bg-soft:#f1f1f1;
  --ink:#3a3a3a;
  --white:#fff;
}
*{box-sizing:border-box;margin:0;padding:0}
html,body{width:882px;height:1200px;overflow:hidden;background:var(--white)}
body{font-family:"Open Sans",Arial,sans-serif;color:var(--grey);font-size:11px;position:relative}
.site-header{height:46px;display:flex;align-items:center;padding:0 36px;background:var(--white)}
.brand{display:flex;align-items:center;gap:7px;font-family:"Montserrat",sans-serif;font-weight:700;font-size:17px;color:var(--green)}
.brand-mark{width:18px;height:18px;background:var(--green);border-radius:3px}
.main-nav{margin-left:auto;display:flex;align-items:center;gap:20px;font-size:10px}
.main-nav a{color:var(--grey);text-decoration:none}
.main-nav a.active{color:var(--green);border-bottom:2px solid var(--green);padding-bottom:3px}
.btn-small{background:var(--green);color:var(--white)!important;font-size:8px;font-weight:600;padding:5px 12px;letter-spacing:.5px}
.hero{position:relative;height:220px;background:linear-gradient(180deg,#8fb83a 0%,#7da32e 55%,#4c5d2a 100%);color:var(--white);text-align:center}
.hero-photo{position:absolute;inset:0;background:linear-gradient(90deg,rgba(40,50,30,.35),rgba(171,208,54,.15) 50%,rgba(40,50,30,.35))}
.hero-inner{position:relative;padding-top:66px}
.hero h1{font-family:"Montserrat",sans-serif;font-weight:600;font-size:19px;letter-spacing:1px}
.search{display:flex;justify-content:center;gap:6px;margin-top:14px}
.search-field{width:360px;height:24px;background:var(--white);border:none}
.search-btn{width:68px;height:24px;background:var(--orange);color:var(--white);font-family:"Montserrat",sans-serif;font-weight:700;font-size:10px;display:flex;align-items:center;justify-content:center}
.usp-band{position:absolute;left:0;right:0;bottom:34px;display:flex;justify-content:center;gap:46px;font-size:10px}
.usp-band span::before{content:"✔ ";color:var(--green)}
.dots{position:absolute;bottom:14px;left:0;right:0;display:flex;justify-content:center;gap:5px}
.dots i{width:6px;height:6px;border-radius:50%;background:var(--white);opacity:.6}
.dots i:first-child{opacity:1}
.stats{background:var(--bg-soft);height:194px;display:flex;justify-content:center;gap:62px;padding-top:46px}
.stat{text-align:center;width:80px}
.stat-icon{width:64px;height:64px;border-radius:50%;background:var(--orange);margin:0 auto 8px;display:flex;align-items:center;justify-content:center}
.stat h3{font-size:10px;font-weight:600;color:var(--ink)}
.stat p{font-size:9px;color:var(--orange)}
.testimonials{padding:26px 60px 0;height:210px;text-align:center}
.section-title{font-family:"Montserrat",sans-serif;font-weight:600;font-size:22px;color:var(--green);letter-spacing:.5px}
.quotes{display:flex;gap:40px;margin-top:18px}
.quote{flex:1}
.quote h4{font-family:"Montserrat",sans-serif;font-size:18px;color:var(--green);font-weight:600;margin-bottom:8px}
.quote p{font-size:9.5px;line-height:1.55}
.quote cite{display:block;font-style:normal;font-size:9px;margin-top:10px;color:var(--ink)}
.newsletter{background:var(--orange);height:50px;display:flex;align-items:center;padding:0 60px;gap:20px;color:var(--white)}
.newsletter strong{font-size:12px;font-weight:600;white-space:nowrap}
.news-field{flex:1;height:22px;background:var(--white)}
.news-btn{width:46px;height:22px;background:var(--green);font-weight:700;font-size:10px;display:flex;align-items:center;justify-content:center}
.site-footer{display:grid;grid-template-columns:1.6fr .8fr 1fr 1fr 1.1fr;gap:22px;padding:32px 60px 0;height:398px}
.site-footer h5{font-family:"Montserrat",sans-serif;font-size:11px;color:var(--green);font-weight:600;margin-bottom:10px}
.site-footer p,.site-footer li{font-size:8.5px;line-height:1.7}
.site-footer ul{list-style:none}
.login-link{color:var(--orange);font-weight:600}
.bottom-bar{position:absolute;bottom:0;left:0;right:0;height:40px;border-top:1px solid var(--grey-light);display:flex;align-items:center;padding:0 60px;font-size:8.5px}
.social{margin-left:auto;display:flex;gap:6px}
.social i{width:14px;height:14px;border-radius:50%;background:var(--grey-light)}
</style>
</head>
<body>
<header class="site-header">
  <div class="brand"><span class="brand-mark"></span>TrimTable</div>
  <nav class="main-nav">
    <a class="active">Home</a><a>About Us</a><a>Our Services</a><a>Testimonials</a><a>Contact Us</a>
    <a class="btn-small">LOGIN</a><a class="btn-small">REGISTER</a>
  </nav>
</header>

<section class="hero">
  <div class="hero-photo" role="img" aria-label="Interieur van een kapsalon met stoelen en spiegels, groen getint"></div>
  <div class="hero-inner">
    <h1>SEARCH &amp; FIND HAIRDRESSER</h1>
    <div class="search"><div class="search-field"></div><div class="search-btn">SEARCH</div></div>
  </div>
  <div class="usp-band"><span>Grootste kapperboekingsite van NL</span><span>Afspraak met 100% zekerheid</span><span>Meer dan 40.000 kapper-reviews</span></div>
  <div class="dots"><i></i><i></i><i></i></div>
</section>

<section class="stats">
  <div class="stat"><div class="stat-icon"><svg width="28" height="28" viewBox="0 0 28 28" fill="none" stroke="#fff" stroke-width="2"><path d="M5 24V11l9-6 9 6v13M11 24v-7h6v7"/></svg></div><h3>Salons</h3><p>12.173</p></div>
  <div class="stat"><div class="stat-icon"><svg width="28" height="28" viewBox="0 0 28 28" fill="none" stroke="#fff" stroke-width="2"><rect x="5" y="6" width="18" height="16" rx="1"/><path d="M9 11h10M9 15h10M9 19h6"/></svg></div><h3>Treatments for booking</h3><p>32.589</p></div>
  <div class="stat"><div class="stat-icon"><svg width="28" height="28" viewBox="0 0 28 28" fill="none" stroke="#fff" stroke-width="2"><rect x="5" y="7" width="18" height="16" rx="1"/><path d="M5 12h18M10 4v5M18 4v5"/></svg></div><h3>Agreements</h3><p>1717</p></div>
  <div class="stat"><div class="stat-icon"><svg width="28" height="28" viewBox="0 0 28 28" fill="none" stroke="#fff" stroke-width="2"><path d="M14 5l2.7 5.6 6.1.9-4.4 4.3 1 6.1-5.4-2.9-5.4 2.9 1-6.1-4.4-4.3 6.1-.9z"/></svg></div><h3>Hairdresser Reviews</h3><p>40.000</p></div>
  <div class="stat"><div class="stat-icon"><svg width="28" height="28" viewBox="0 0 28 28" fill="none" stroke="#fff" stroke-width="2.4"><path d="M7 14l5 5 9-10"/></svg></div><h3>Reliable Reviews</h3><p>100%</p></div>
</section>

<section class="testimonials">
  <h2 class="section-title">CLIENT TESTIMONIALS</h2>
  <div class="quotes">
    <article class="quote"><h4>Fantastisch!</h4><p>"Heerlijk hoe eenvoudig ik een afspraak kan maken. In een paar klikken had ik mijn kapper geboekt en kreeg ik direct een bevestiging."</p><cite>Eva, Utrecht</cite></article>
    <article class="quote"><h4>Superfijn!</h4><p>"Superfijn dat ik alle kappers in mijn buurt kan vergelijken en meteen zie wanneer er plek is."</p><cite>Lotte, Zwolle</cite></article>
    <article class="quote"><h4>Handige Recensies</h4><p>"Dankzij de eerlijke recensies wist ik precies waar ik naartoe moest. Mijn nieuwe kapsalon is een echte aanrader geworden."</p><cite>Joris, Amsterdam</cite></article>
  </div>
</section>

<section class="newsletter">
  <strong>Leuke TrimTable tips krijgen? Schrijf je in!</strong>
  <div class="news-field"></div><div class="news-btn">GO</div>
</section>

<footer class="site-footer">
  <div><h5>Boek een afspraak bij de kapper in een van deze steden</h5><p>Via TrimTable vind je snel een kapper bij jou in de buurt. Vergelijk salons, lees echte reviews en kies het moment dat jou het beste uitkomt. Je afspraak staat direct vast en je ontvangt meteen een bevestiging per mail.</p></div>
  <div><h5>Quick Links</h5><ul><li>Beleidsverklaring</li><li>Over ons</li><li>Hoe werkt het</li></ul></div>
  <div><h5>Locations</h5><ul><li>Kapper Amsterdam</li><li>Kapper Rotterdam</li><li>Kapper Den Haag</li><li>Kapper Utrecht</li><li>Kapper Eindhoven</li><li>Kapper Tilburg</li><li>Kapper Almere</li></ul></div>
  <div><h5>&nbsp;</h5><ul><li>Kapper Groningen</li><li>Kapper Arnhem</li><li>Kapper Breda</li><li>Kapper Nijmegen</li><li>Kapper Haarlem</li></ul></div>
  <div><h5>Ben je de ondernemer in een van deze kapsalons?</h5><p>Kapper? <span class="login-link">Log hier in</span></p></div>
</footer>

<div class="bottom-bar"><span>2015 (c) Disclaimer | TrimTable</span><div class="social"><i></i><i></i><i></i></div></div>
</body>
</html>
```